Maple Gable Business Card

Colors can be blue, grey and white as you see in the attached logo. Needs to have a spot for name, title, phone, email, address, and website. There also needs to be a spot for an agent's picture.

Contact Information for Business Card

See project description.

Colors

Designer to choose colors to be used in the design.

```html
<!DOCTYPE html>
<html lang="en">
<head>
<meta charset="utf-8">
<title>Maple Gable Business Card</title>
<link href="https://fonts.googleapis.com/css2?family=Montserrat:wght@300;400;600&display=swap" rel="stylesheet">
<style>
  :root {
    --stage: #1c1c1c;
    --card-dark: #262626;
    --card-dark-edge: #333333;
    --card-light: #ffffff;
    --brand-blue: #2f74b8;
    --ink: #3a3a3a;
    --photo-top: #d9dee4;
    --photo-bottom: #b7bfc8;
  }
  * { margin: 0; padding: 0; box-sizing: border-box; }
  html, body {
    width: 1200px; height: 900px; overflow: hidden;
    background: var(--stage);
    font-family: "Montserrat", sans-serif;
  }
  .stage {
    position: relative; width: 1200px; height: 900px;
    display: flex; flex-direction: column; align-items: center; justify-content: center; gap: 28px;
  }
  .card {
    position: relative;
    width: 740px; height: 400px;
    box-shadow: 0 14px 30px rgba(0,0,0,0.55);
    display: flex; flex-direction: column; align-items: center; justify-content: center;
  }
  .card-front {
    background: linear-gradient(135deg, var(--card-dark) 0%, var(--card-dark-edge) 100%);
  }
  .front-wordmark {
    color: var(--brand-blue);
    font-weight: 600; font-size: 58px; letter-spacing: 2px;
    text-transform: uppercase;
  }
  .card-back { background: var(--card-light); }
  .agent-photo {
    position: absolute; left: 52px; top: 50%;
    width: 140px; height: 140px; margin-top: -70px;
    border-radius: 50%;
    background: linear-gradient(180deg, var(--photo-top), var(--photo-bottom));
    border: 3px solid var(--brand-blue);
  }
  .back-content {
    display: flex; flex-direction: column; align-items: center;
    margin-left: 150px;
  }
  .back-brand {
    display: flex; align-items: center; gap: 12px; margin-bottom: 16px;
  }
  .brand-square { width: 20px; height: 20px; background: var(--brand-blue); }
  .back-wordmark {
    color: var(--brand-blue); font-weight: 600; font-size: 30px;
    letter-spacing: 1px; text-transform: uppercase;
  }
  .agent-name {
    color: var(--brand-blue); font-weight: 600; font-size: 27px;
    letter-spacing: 1.5px; text-transform: uppercase;
  }
  .agent-title {
    color: var(--ink); font-weight: 400; font-size: 18px; margin-top: 2px;
  }
  .contact-icons { display: flex; gap: 10px; margin: 12px 0 6px; }
  .contact-icons svg { width: 22px; height: 22px; }
  .contact-list {
    list-style: none; text-align: center;
    color: var(--ink); font-weight: 400; font-size: 19px; line-height: 1.34; letter-spacing: 1px;
  }
  .contact-list .accent { color: var(--brand-blue); }
</style>
</head>
<body>
<main class="stage">
  <section class="card card-front">
    <p class="front-wordmark">Maple Gable</p>
  </section>

  <section class="card card-back">
    <div class="agent-photo" role="img" aria-label="Agent portrait photo"></div>
    <div class="back-content">
      <div class="back-brand">
        <span class="brand-square"></span>
        <span class="back-wordmark">Maple Gable</span>
      </div>
      <h1 class="agent-name">Daniel Mercer</h1>
      <p class="agent-title">Director</p>
      <div class="contact-icons">
        <svg viewBox="0 0 24 24" aria-label="Phone"><circle cx="12" cy="12" r="10.5" fill="none" stroke="#2f74b8" stroke-width="1.5"/><path d="M9 7c-1 0-1.6 1-1.4 2 .6 3.4 3.4 6.3 6.8 7 1 .2 2-.4 2-1.4l-1.8-1.3-1.2 1c-1.5-.7-2.7-2-3.4-3.4l1-1.2z" fill="#2f74b8"/></svg>
        <svg viewBox="0 0 24 24" aria-label="Email"><circle cx="12" cy="12" r="10.5" fill="none" stroke="#2f74b8" stroke-width="1.5"/><rect x="6.5" y="8.5" width="11" height="7.5" fill="none" stroke="#2f74b8" stroke-width="1.3"/><path d="M6.5 8.5l5.5 4.2 5.5-4.2" fill="none" stroke="#2f74b8" stroke-width="1.3"/></svg>
        <svg viewBox="0 0 24 24" aria-label="Website"><circle cx="12" cy="12" r="10.5" fill="none" stroke="#2f74b8" stroke-width="1.5"/><circle cx="12" cy="12" r="6" fill="none" stroke="#2f74b8" stroke-width="1.2"/><ellipse cx="12" cy="12" rx="2.6" ry="6" fill="none" stroke="#2f74b8" stroke-width="1.2"/><path d="M6 12h12M7 9h10M7 15h10" stroke="#2f74b8" stroke-width="1"/></svg>
        <svg viewBox="0 0 24 24" aria-label="Address"><circle cx="12" cy="12" r="10.5" fill="none" stroke="#2f74b8" stroke-width="1.5"/><path d="M12 18s-4.5-4.6-4.5-7.8a4.5 4.5 0 0 1 9 0C16.5 13.4 12 18 12 18z" fill="#2f74b8"/><circle cx="12" cy="10.2" r="1.6" fill="#ffffff"/></svg>
      </div>
      <ul class="contact-list">
        <li>(123) 555-0142</li>
        <li>info@maplegable.com</li>
        <li>www.<span class="accent">maplegable</span>.com</li>
        <li>48 Linden Lane, Brookfield</li>
      </ul>
    </div>
  </section>
</main>
</body>
</html>
```